Re-Design an adult education portal

I need support to re-design an adult education portal. Currently the customer has an incomplete website which should be prepared in a new format.
I have the idea how to realize, but I have no clue how to design it. The hard thing is to have a "beautiful" website with available logo and main color. I hope you can support me.

Name of Website: moluvo (moluvo.ch)
Content: adult eduction for adult in safety at work, mountain climbing, dog school. various courses in different areas. But on old webpage is hard to find the different possibilities.
main color: Ral 6011 (green) -> #6C7C59
logo: you see on top of website the logo (2 dogs and a mountain with a colour gradient).

new website: for new webpage I decided to have a navigation for each section of education. In the main area I would like to have some pictures to give an idea what content is behind. At the moment it looks terrible, so I decided to use you as support for me to make the webpage prettier :). And maybe you have an better idea how to make it great. -> current state of new web page: https://moluvo.perch-net.ch/

Target Market(s)

adult eduction for adult in safety at work, mountain climbing, dog school

Number of Pages Required

1 page

Font styles to use
Serif
Sans Serif

Requirements
Must have
• As main color is set "Ral 6011" (green) -> #6C7C59

```html
<!DOCTYPE html>
<html lang="en">
<head>
<meta charset="utf-8">
<title>moluvo.ch – Your training and course partner</title>
<link href="https://fonts.googleapis.com/css2?family=Comfortaa:wght@400;600;700&family=Open+Sans:wght@400;600;700&display=swap" rel="stylesheet">
<style>
:root{
  --green:#6C7C59;
  --green-dark:#4f5c40;
  --mint:#eef5e4;
  --ink:#2b2b2b;
  --muted:#8a8a8a;
  --line:#d6d6d6;
  --footer:#1c1c1c;
  --white:#ffffff;
}
*{box-sizing:border-box;margin:0;padding:0}
html,body{width:1200px;height:3160px;overflow:hidden}
body{font-family:"Open Sans",Arial,sans-serif;color:var(--ink);background:var(--white);position:relative}
.heading{font-family:"Comfortaa",Arial,sans-serif;font-weight:400}
.btn{display:inline-block;background:var(--green-dark);color:var(--white);font-size:13px;font-weight:700;letter-spacing:.5px;text-transform:uppercase;border-radius:30px;padding:16px 34px;text-decoration:none}

/* header */
.site-header{position:absolute;top:0;left:0;width:1200px;height:64px;background:var(--white);z-index:5}
.brand{position:absolute;top:0;left:0;width:230px;height:110px;background:var(--white);border-bottom-right-radius:60px;z-index:6;display:flex;align-items:center;padding-left:26px;gap:10px}
.brand-dot{width:14px;height:14px;border-radius:50%;background:var(--green)}
.brand-name{font-family:"Comfortaa",Arial,sans-serif;font-weight:700;font-size:34px;color:var(--green-dark)}
.main-nav{position:absolute;right:48px;top:18px;display:flex;align-items:center;gap:30px;font-size:14px}
.main-nav a{color:var(--ink);text-decoration:none}
.main-nav a.active{border-bottom:2px solid var(--green);padding-bottom:4px}
.main-nav .btn{padding:9px 22px;font-size:12px}

/* hero */
.hero{position:absolute;top:64px;left:0;width:1200px;height:700px;background:linear-gradient(120deg,#5d6e45 0%,#8ea36a 35%,#6b6a55 65%,#3f4a33 100%)}
.hero-title{position:absolute;left:140px;top:170px;font-size:66px;line-height:1.12;color:var(--white)}
.hero .btn{position:absolute;left:140px;top:440px}
.slider-dots{position:absolute;right:42px;top:300px;display:flex;flex-direction:column;gap:12px}
.slider-dots span{width:8px;height:8px;border-radius:50%;background:var(--white);opacity:.7}
.slider-dots span:first-child{opacity:1}
.hero-cut{position:absolute;left:0;top:620px;width:1200px;height:150px}

/* about */
.about-photo{position:absolute;left:0;top:700px;width:480px;height:500px;background:linear-gradient(160deg,#6a7a8a 0%,#9a8a6e 45%,#4a4030 100%)}
.about-text{position:absolute;left:560px;top:760px;width:560px}
.about-text h2{font-size:58px;margin-bottom:30px}
.about-text p{font-size:13px;line-height:1.9;color:var(--muted);margin-bottom:40px}

/* services */
.services{position:absolute;left:0;top:1200px;width:1200px;height:1020px;background:var(--mint)}
.services h2{position:absolute;top:70px;width:100%;text-align:center;font-size:58px}
.service{position:absolute;width:284px;height:284px;border-radius:50%;display:flex;align-items:center;justify-content:center;text-align:center;color:var(--white);font-weight:700;font-size:16px;line-height:1.4;text-transform:uppercase;box-shadow:0 4px 14px rgba(0,0,0,.2)}
.service span{position:relative;top:50px}
.s1{left:146px;top:220px;background:radial-gradient(circle,#3d3d3d,#1e1e1e)}
.s2{left:458px;top:220px;background:radial-gradient(circle,#7a8088,#3a3e44)}
.s3{left:770px;top:220px;background:radial-gradient(circle,#5a6a7a,#2e3430)}
.s4{left:146px;top:520px;background:radial-gradient(circle,#6f8a4e,#2f3a22)}
.s5{left:458px;top:520px;background:radial-gradient(circle,#5a6a70,#262a2c)}
.s6{left:770px;top:520px;background:radial-gradient(circle,#8a96a6,#3c4450)}
.services .btn{position:absolute;left:504px;top:854px}

/* contact */
.contact{position:absolute;left:0;top:2220px;width:1200px;height:600px}
.contact h2{position:absolute;top:80px;width:100%;text-align:center;font-size:58px}
.contact-form{position:absolute;left:232px;top:198px;width:736px}
.row{display:flex;gap:16px;margin-bottom:16px}
.field{flex:1;height:56px;border:1px solid var(--line);padding:16px;font-size:13px;color:var(--muted)}
.field.message{height:116px}
.form-actions{text-align:center;margin-top:24px}

/* footer */
.site-footer{position:absolute;left:0;top:2770px;width:1200px;height:390px}
.footer-bg{position:absolute;left:0;top:0}
.socials{position:absolute;top:150px;left:0;width:100%;display:flex;justify-content:center;gap:18px}
.socials span{width:40px;height:40px;border-radius:50%;border:1px solid var(--white)}
.contact-line{position:absolute;top:220px;width:100%;text-align:center;color:var(--white);font-size:14px;font-weight:600}
.contact-line svg{vertical-align:-2px;margin-right:6px}
.contact-line .sep{margin:0 12px;opacity:.6}
.footer-nav{position:absolute;top:270px;width:100%;text-align:center;color:var(--white);font-size:14px;font-weight:700;letter-spacing:.5px}
.footer-nav .sep{margin:0 10px}
.copyright{position:absolute;top:314px;width:100%;text-align:center;color:#bdbdbd;font-size:11px}
</style>
</head>
<body>

<header class="site-header">
  <nav class="main-nav">
    <a class="active" href="#">Home</a>
    <a href="#">Occupational safety</a>
    <a href="#">First aid</a>
    <a href="#">Dog school</a>
    <a href="#">CZV</a>
    <a href="#">Mountain training</a>
    <a class="btn" href="#">Login</a>
  </nav>
</header>
<div class="brand"><span class="brand-dot"></span><span class="brand-name">moluvo.ch</span></div>

<section class="hero" role="img" aria-label="Two course trainers sitting outdoors with their dogs in front of a green mountain landscape">
  <h1 class="hero-title heading">Your training<br>and course<br>partner</h1>
  <a class="btn" href="#">Get started</a>
  <div class="slider-dots"><span></span><span></span><span></span><span></span></div>
</section>
<svg class="hero-cut" width="1200" height="150" viewBox="0 0 1200 150"><polygon points="0,100 1200,0 1200,150 0,150" fill="#ffffff"/></svg>

<section class="about">
  <div class="about-photo" role="img" aria-label="The trainers with several dogs in front of a tree and mountains"></div>
  <div class="about-text">
    <h2 class="heading">About Us</h2>
    <p>In our professional career, we have repeatedly faced situations that called for calm action and solid knowledge. Our courses combine practical training with clear theory, so that participants feel safe and confident when it matters most. We believe that well prepared people act better in an emergency and protect the ones around them.</p>
    <a class="btn" href="#">Read more</a>
  </div>
</section>

<section class="services">
  <h2 class="heading">What We Do</h2>
  <div class="service s1" role="img" aria-label="Forklift in a warehouse"><span>Forklift<br>courses</span></div>
  <div class="service s2" role="img" aria-label="Personal protective equipment"><span>PPE</span></div>
  <div class="service s3" role="img" aria-label="Aerial work platform at a building site"><span>Aerial work<br>platform</span></div>
  <div class="service s4" role="img" aria-label="Dogs training on a meadow"><span>Dog school</span></div>
  <div class="service s5" role="img" aria-label="First aid course in a classroom"><span>First aiders</span></div>
  <div class="service s6" role="img" aria-label="Medical training group"><span>Medical<br>training</span></div>
  <a class="btn" href="#">View more</a>
</section>

<section class="contact">
  <h2 class="heading">Get in Touch</h2>
  <form class="contact-form">
    <div class="row"><div class="field">First Name</div><div class="field">Last Name</div></div>
    <div class="row"><div class="field">Email Address</div><div class="field">Phone Number</div></div>
    <div class="row"><div class="field message">Message</div></div>
    <div class="form-actions"><a class="btn" href="#">Submit message</a></div>
  </form>
</section>

<footer class="site-footer">
  <svg class="footer-bg" width="1200" height="390" viewBox="0 0 1200 390"><polygon points="0,60 1200,0 1200,390 0,390" fill="#1c1c1c"/></svg>
  <div class="socials"><span></span><span></span><span></span><span></span></div>
  <div class="contact-line">
    <svg width="12" height="14" viewBox="0 0 12 14"><path d="M6 0a5 5 0 0 0-5 5c0 4 5 9 5 9s5-5 5-9a5 5 0 0 0-5-5zm0 7a2 2 0 1 1 0-4 2 2 0 0 1 0 4z" fill="#fff"/></svg>Lindenweg 12, CH-3900 Brig
    <span class="sep">|</span>
    <svg width="13" height="13" viewBox="0 0 13 13"><path d="M3 0l2 3-1.5 1.5a8 8 0 0 0 5 5L10 8l3 2-1 3C6 13 0 7 0 1z" fill="#fff"/></svg>Phone: +41 79 000 12 34
    <span class="sep">|</span>
    <svg width="14" height="11" viewBox="0 0 14 11"><rect x=".5" y=".5" width="13" height="10" fill="none" stroke="#fff"/><path d="M.5.5l6.5 5 6.5-5" fill="none" stroke="#fff"/></svg>Email: info@moluvo.ch
  </div>
  <div class="footer-nav">HOME<span class="sep">/</span>OCCUPATIONAL SAFETY<span class="sep">/</span>FIRST AID<span class="sep">/</span>DOG SCHOOL<span class="sep">/</span>CZV<span class="sep">/</span>MOUNTAIN TRAINING</div>
  <div class="copyright">© 2021 Copyright moluvo All Rights Reserved &nbsp;|&nbsp; Privacy Policy &nbsp;|&nbsp; Terms</div>
</footer>

</body>
</html>
```